Website for a Psychologist in Private Practice

I need a cool web design for my website: www.drkalvoric.com. I would like it to look professional. Keep all the current content and add: Space for video; radio spots (see Silver Cedar Tunes Logo below for those); Quick Inquiry; Friendora link; 5 star rating on Rivo; a map; reviews from former patients. I am open to suggestions.

Target Market(s)

Those seeking individual and marital counseling.

Industry/Entity Type

Mental Health

Number of Pages Required

1 page

Font styles to use
Sans Serif
Other font styles liked:
• I'm open but no hard to read script

Requirements
Must have
• All the content on my home page with link for video and radio spots. List services and degrees and expertices (pics not necessary).
Nice to have
• A video of me and radio conversations (logo of Silver Cedar Tunes radio attached).
Should not have
• Cartoons, comedy, etc.... I don't need pictures of services (marital, depression, etc...) Just list those.

```html
<!DOCTYPE html>
<html lang="en">
<head>
<meta charset="utf-8">
<title>Dr. Lorna V. Kalvoric — Psychologist</title>
<link href="https://fonts.googleapis.com/css2?family=Ubuntu:wght@400;500&family=Raleway:wght@400;500&family=Arimo:ital,wght@0,400;0,700;1,400;1,700&display=swap" rel="stylesheet">
<style>
:root{
  --sky:#5f8fb5;
  --sea:#3aa3ad;
  --sand:#cfb394;
  --sand-light:#dcc5aa;
  --header-glass:rgba(30,60,95,.55);
  --green:#1fae52;
  --blue:#2a7fc1;
  --ink:#333;
  --dark-footer:#262626;
  --field-top:#2b2f33;
  --field-bottom:#6b5430;
  --white:#fff;
}
*{margin:0;padding:0;box-sizing:border-box}
html,body{width:744px;height:1200px;overflow:hidden;background:#fff}
body{font-family:"Arimo",Arial,sans-serif;color:var(--ink)}
.page{position:relative;width:744px;height:1200px;overflow:hidden}
.abs{position:absolute}
.beach-bg{left:0;top:0;width:744px;height:560px;
  background:linear-gradient(180deg,var(--sky) 0%,#7fb4cf 12%,var(--sea) 22%,#7cc3c4 32%,#d8c7ae 45%,var(--sand) 70%,var(--sand-light) 100%)}
.header{left:82px;top:0;width:581px;height:86px;background:var(--header-glass)}
.avatar{left:87px;top:6px;width:76px;height:76px;border-radius:50%;border:3px solid #fff;background:linear-gradient(160deg,#c9a98a,#7a8fa4)}
.brand-name{left:174px;top:26px;font-family:"Ubuntu",sans-serif;font-size:24px;color:#fff;font-weight:500}
.brand-license{left:176px;top:55px;font-family:"Ubuntu",sans-serif;font-size:10px;color:#fff}
.call{left:543px;top:31px;color:#fff}
.call svg{position:absolute;left:0;top:4px}
.call-label{position:absolute;left:25px;top:0;font-size:9.5px;white-space:nowrap}
.call-number{position:absolute;left:27px;top:13px;font-size:14px;white-space:nowrap}
.slider{left:82px;top:86px;width:581px;height:272px;background:radial-gradient(ellipse at 60% 45%,#e3c7b0 0%,#8fb545 40%,#4e7e1e 100%);box-shadow:0 6px 8px rgba(0,0,0,.35)}
.slide-arrow{top:124px;width:22px;height:22px;background:rgba(40,40,40,.75);display:flex;align-items:center;justify-content:center}
.slide-caption{left:18px;top:183px;font-family:"Ubuntu",sans-serif;font-size:21px;line-height:32px;color:#fff;text-shadow:0 1px 3px rgba(0,0,0,.5)}
.section-head{left:82px;top:372px;width:581px;height:26px;border-bottom:1px dashed #555}
.section-head h2{position:absolute;left:1px;top:0;font-family:"Raleway",sans-serif;font-weight:400;font-size:16px;color:#333}
.section-head span{position:absolute;right:4px;top:4px;font-family:"Ubuntu",sans-serif;font-size:10px;color:#333}
.skill{top:415px;width:140px;text-align:center}
.skill .ring{width:74px;height:74px;margin:0 auto;border-radius:50%;border:3px solid var(--blue);background:#fff;display:flex;align-items:center;justify-content:center;box-shadow:0 3px 4px rgba(0,0,0,.25)}
.skill .ring.active{border-color:var(--green)}
.skill .glyph{width:44px;height:44px;border-radius:50%;background:#3a3a3a}
.skill p{margin-top:17px;font-family:"Raleway",sans-serif;font-weight:500;font-size:11px;line-height:14px;color:#222}
.degrees{left:0;top:560px;width:744px;height:49px;background:var(--green);color:#fff}
.degrees h3{position:absolute;left:118px;top:15px;font-family:"Ubuntu",sans-serif;font-weight:500;font-size:14px}
.degrees svg.brace{position:absolute;left:205px;top:9px}
.degree{position:absolute;font-size:8.5px;white-space:nowrap;padding-left:13px}
.degree:before{content:"";position:absolute;left:1px;top:1px;width:4px;height:7px;border:solid #fff;border-width:0 1.5px 1.5px 0;transform:rotate(45deg)}
.field{left:0;top:609px;width:744px;height:225px;background:linear-gradient(180deg,var(--field-top) 0%,#3d3b36 30%,#7a6a45 55%,var(--field-bottom) 100%)}
.col-title{top:630px;width:180px;height:25px;border-bottom:1px dashed #888;font-family:"Raleway",sans-serif;font-weight:500;font-size:14.5px;color:#fff}
.video{left:82px;top:665px;width:182px;height:139px;border:2px solid #ddd;background:linear-gradient(160deg,#6d7f92,#c7a98b 55%,#3e5b85)}
.play{left:73px;top:54px;width:20px;height:20px;border:2px solid #fff;border-radius:50%}
.play:after{content:"";position:absolute;left:6px;top:3.5px;border-left:7px solid #fff;border-top:4.5px solid transparent;border-bottom:4.5px solid transparent}
.form-intro{left:288px;top:668px;font-size:7.5px;color:#fff}
.input{left:283px;width:180px;background:rgba(120,120,120,.55);font-size:8px;color:#fff;padding:4px 5px}
.submit{left:283px;top:786px;width:68px;height:19px;background:var(--blue);color:#fff;font-size:9.5px;font-weight:700;text-align:center;line-height:19px}
.quote-mark{left:483px;top:660px;font-family:Georgia,serif;font-size:20px;color:#aaa}
.quote{left:483px;top:669px;width:180px;font-size:8.6px;line-height:13.1px;font-style:italic;color:#fff;text-indent:14px}
.quote-author{left:617px;top:780px;font-size:8.6px;color:#fff}
.view-all{left:487px;top:789px;font-size:8.6px;color:#fff;text-decoration:underline}
.reviews-title{left:0;top:860px;width:744px;text-align:center;font-family:"Ubuntu",sans-serif;font-size:13.5px;color:#222}
.reviews-rule{left:278px;top:881px;width:189px;height:1px;background:#bbb}
.reviews-rule-accent{left:350px;top:880px;width:45px;height:3px;background:var(--blue)}
.patient{left:89px;top:898px;width:70px;height:70px;border-radius:50%;background:linear-gradient(160deg,#b49780,#2d3440 70%)}
.review-text{left:172px;top:902px;width:490px;font-size:8.3px;line-height:14.6px;font-style:italic;color:#222;text-indent:24px}
.review-sign{left:174px;top:970px;font-size:8.3px;font-weight:700;font-style:italic}
.read-more{left:563px;top:982px;font-size:8.3px;color:#444}
.read-more u{color:#444}
.footer{left:0;top:1022px;width:744px;height:152px;background:var(--dark-footer);color:#fff}
.f-title{position:absolute;font-family:"Raleway",sans-serif;font-size:10px;font-weight:500}
.f-title.line{border-bottom:1px dashed #777;padding-bottom:4px}
.links{position:absolute;left:83px;top:43px;list-style:none;font-size:8px;line-height:13.6px}
.links li:first-child{color:#e08e5a}
.partner{position:absolute;top:43px;height:35px;border:1px solid #888}
.rating-badge{position:absolute;left:188px;top:92px;width:50px;height:48px;border-radius:7px;background:#c8102e;border:2px solid #eee}
.share-label{position:absolute;left:252px;top:101px;font-size:10px;font-family:"Raleway",sans-serif}
.share-btn{position:absolute;left:252px;top:117px;width:57px;height:20px;background:#3b5c9a;border:1px solid #8aa;font-size:7.5px;color:#fff;display:flex;align-items:center;padding-left:6px;gap:5px}
.share-btn i{width:8px;height:8px;background:#fff;display:block}
.contact{position:absolute;left:404px;font-size:8px;line-height:11.5px}
.contact b{position:absolute;left:0;font-weight:400}
.contact span{position:absolute;left:18px;white-space:nowrap}
.radio-show{position:absolute;left:553px;top:24px;width:106px;height:106px;background:linear-gradient(160deg,#d9306f 0%,#c46a7c 35%,#5c6a6e 100%)}
.radio-name{position:absolute;left:0;top:3px;width:106px;text-align:center;font-family:"Arimo",sans-serif;font-weight:700;font-size:8.5px;color:#fff}
.copyright{left:0;top:1174px;width:744px;height:26px;background:var(--blue);color:#fff;font-size:8px;text-align:center;line-height:26px}
</style>
</head>
<body>
<div class="page">
  <div class="abs beach-bg" role="img" aria-label="Background photo of a tropical beach with turquoise sea and sand"></div>

  <header class="abs header">
  </header>
  <div class="abs avatar" role="img" aria-label="Portrait photo of Dr. Kalvoric"></div>
  <div class="abs brand-name">Dr. Lorna V. Kalvoric</div>
  <div class="abs brand-license">California # PSY20581</div>
  <div class="abs call">
    <svg width="20" height="20" viewBox="0 0 20 20"><circle cx="10" cy="10" r="9" fill="none" stroke="#fff" stroke-width="1.2"/><path d="M7 5.5c-.8.6-1 1.8-.5 3.3.8 2.3 2.5 4.5 4.4 5.6 1.1.6 2.1.5 2.7-.2l-1.6-1.7-1 .5c-1-.6-2-1.9-2.4-3.1l.8-.7z" fill="#fff"/></svg>
    <span class="call-label">Call Us Today</span>
    <span class="call-number">555-214-7830</span>
  </div>

  <section class="abs slider" role="img" aria-label="Slideshow photo of a joyful woman with arms raised among green trees">
    <div class="abs slide-arrow" style="left:4px"><svg width="8" height="10"><path d="M6 1 2 5l4 4" stroke="#fff" stroke-width="2" fill="none"/></svg></div>
    <div class="abs slide-arrow" style="right:4px"><svg width="8" height="10"><path d="M2 1l4 4-4 4" stroke="#fff" stroke-width="2" fill="none"/></svg></div>
    <div class="abs slide-caption">The Best way to Conquer<br>a problem is to FACE it</div>
  </section>

  <div class="abs section-head"><h2>My Expertise</h2><span>California # PSY20581</span></div>
  <div class="abs skill" style="left:54px"><div class="ring active"><div class="glyph" role="img" aria-label="Icon of a couple"></div></div><p>Dating &amp;<br>Marriage</p></div>
  <div class="abs skill" style="left:180px"><div class="ring"><div class="glyph" role="img" aria-label="Icon of a family"></div></div><p>Parenting &amp; Professional<br>Relationships</p></div>
  <div class="abs skill" style="left:317px"><div class="ring"><div class="glyph" role="img" aria-label="Icon of a person juggling tasks"></div></div><p>Life<br>Management</p></div>
  <div class="abs skill" style="left:442px"><div class="ring"><div class="glyph" role="img" aria-label="Icon of two faces"></div></div><p>Personality<br>Disorders</p></div>
  <div class="abs skill" style="left:549px"><div class="ring"><div class="glyph" role="img" aria-label="Icon of a seated person"></div></div><p>Depression &amp;<br>Anxiety Issues</p></div>

  <section class="abs degrees">
    <h3>My Degrees</h3>
    <svg class="brace" width="12" height="32" viewBox="0 0 12 32"><path d="M2 1c4 0 5 2 5 6v5c0 2 1 4 4 4-3 0-4 2-4 4v5c0 4-1 6-5 6" fill="none" stroke="#cfe9d6" stroke-width="1.3"/></svg>
    <span class="degree" style="left:239px;top:12px">Doctoral Degree in Clinical Psychology</span>
    <span class="degree" style="left:239px;top:29px">Masters Degree in Counseling Psychology</span>
    <span class="degree" style="left:440px;top:12px">Doctoral Internship, Coastline Medical Center</span>
    <span class="degree" style="left:440px;top:29px">Masters Internship, Westbrook Clinic</span>
  </section>

  <div class="abs field" role="img" aria-label="Background photo of a wheat field at sunset"></div>
  <h3 class="abs col-title" style="left:82px">View Video</h3>
  <h3 class="abs col-title" style="left:283px">Quick Inquiry</h3>
  <h3 class="abs col-title" style="left:483px">Radio Conversations</h3>

  <div class="abs video" role="img" aria-label="Video still of Dr. Kalvoric"><div class="abs play"></div></div>

  <div class="abs form-intro">Lorem ipsum dolor sit amet, consectetuer</div>
  <div class="abs input" style="top:684px;height:20px">Name</div>
  <div class="abs input" style="top:706px;height:20px">Email</div>
  <div class="abs input" style="top:728px;height:20px">Phone</div>
  <div class="abs input" style="top:750px;height:31px">Message</div>
  <div class="abs submit">SUBMIT</div>

  <div class="abs quote-mark">“</div>
  <p class="abs quote">Lorem ipsum dolor sit ame onsecte iscingrd elit, sed diam nonummy nibh euis tincidunt ut laoreetlore gna aliquam erat olutpat. Ut wisi fd enim adinim veniam, quis strud xerc ullamrper suscipit lobortis sal wisi ut laoreetlorna aliquam erat olutpat. Utnim adinim veniam, quis strud a xerci gna aliquam erat olutpat. Ut uis strud fd xerci gna aliquam erat olutpat. Utorem.</p>
  <div class="abs quote-author">Mara Quinlan</div>
  <div class="abs view-all">View All</div>

  <h2 class="abs reviews-title">Reviews From Former Patients</h2>
  <div class="abs reviews-rule"></div>
  <div class="abs reviews-rule-accent"></div>
  <div class="abs patient" role="img" aria-label="Portrait photo of a former patient"></div>
  <p class="abs review-text">Lorem ipsum dolor sit amet, consectetuer adipiscing elit, sed diam nonummy nibh euismod tincidunt ut laoreet dolore magna aliquam erat volutpat. Ut wisi enim ad minim veniam, quis nostrud exerci tation ullamcorper suscipit lobortis nisl ut aliquip commodo consequat. Duis autem vel eum iriure dolor in hendrerit in vulputate velit esse molestie consequat, vel illum dolore eu feugiat nulla facilisis at vero eros et accumsan et iusto odio dignissimaugue duis dolore te feugait nulla facilisi.</p>
  <div class="abs review-sign">.... Lorem Ispum, Manger</div>
  <div class="abs read-more"><u>Read more testimonials</u> »</div>

  <footer class="abs footer">
    <div class="f-title line" style="left:83px;top:18px;width:72px">Quick Links</div>
    <ul class="links">
      <li>Home</li><li>About Me</li><li>Sessions</li><li>Resources</li><li>BIO</li><li>Customer Reviews</li><li>Contact Me</li>
    </ul>
    <div class="f-title" style="left:188px;top:18px">A Portion of All Revenue is Donated to</div>
    <div class="partner" style="left:188px;width:89px;background:#fff" role="img" aria-label="Partner charity badge"></div>
    <div class="partner" style="left:283px;width:89px;background:#7f9a3a" role="img" aria-label="Partner charity badge"></div>
    <div class="rating-badge" role="img" aria-label="Rivo five star rating badge"></div>
    <div class="share-label">Friendora share</div>
    <div class="share-btn"><i></i>SHARE</div>
    <div class="f-title line" style="left:404px;top:18px;width:118px">Contact Details</div>
    <div class="contact" style="top:86px"><b>A:</b><span style="left:18px">418 Harbor Lane, Suite 120<br>Seabright Cove, CA 90410</span></div>
    <div class="contact" style="top:128px"><b>P:</b><span>555-214-7830</span></div>
    <div class="contact" style="top:149px"><b>TF:</b><span style="left:20px">555-214-7830</span></div>
    <div class="contact" style="top:170px"><b>E:</b><span>lk@drkalvoric.com</span></div>
    <div class="radio-show" role="img" aria-label="Promo photo for the Silver Cedar Tunes radio show with its two hosts">
      <div class="radio-name">Silver Cedar Tunes</div>
    </div>
  </footer>

  <div class="abs copyright">Copyright © 2016 Dr. Lorna V. Kalvoric&nbsp; All rights reserved</div>
</div>
</body>
</html>
```